3rd Annual Suds & Wags Fundraiser

This is our 3rd Annual Suds & Wags Dog Wash Extravagana to support Helpers of Tamsin Valley Pet Center. Please see the attached flyer for the 2nd Annual. We loved this flyer! Please revamp with our logo attached and the new content provided. Let's keep to the same colors as the 2nd Annual flyer-no change. Date: Saturday April 25th 2020 10A-1PM. Rain Date: May 2nd. Same address as 2nd Annual.

Other font styles liked:
• See 2nd Annual Flyer

Colors
add136
e34297
6b449b

Requirements
Must have
• See attached 2nd annual flyer including colors
Nice to have

```html
<!DOCTYPE html>
<html lang="en">
<head>
<meta charset="utf-8">
<title>Suds &amp; Wags Doggie Wash Extravaganza</title>
<link rel="stylesheet" href="https://fonts.googleapis.com/css2?family=Fredoka:wght@600;700&family=Montserrat:ital,wght@0,400;0,500;0,600;0,700;0,800;1,400&display=swap">
<style>
:root{
  --green:#9bc33b;
  --green-bright:#add136;
  --pink:#e34297;
  --purple:#8a6bb4;
  --purple-deep:#6b449b;
  --ink:#1d1d1d;
  --navy:#2b3a8c;
  --band:#e2e2e2;
  --page:#d9d9d9;
  --white:#ffffff;
}
*{margin:0;padding:0;box-sizing:border-box}
html,body{width:703px;height:1200px;overflow:hidden;background:var(--page)}
body{font-family:"Montserrat",sans-serif;color:var(--ink);position:relative}
.flyer{position:absolute;left:0;top:103px;width:775px;height:1095px;transform:scale(.9071);transform-origin:0 0;background:var(--white);overflow:hidden;box-shadow:0 4px 14px rgba(0,0,0,.18)}
.flyer > *{position:absolute}
.backdrop{left:0;top:0;width:775px;height:1095px}
.photo{background:linear-gradient(160deg,#5f8a3a 0%,#8fae6a 35%,#9aa0b5 65%,#4d5b8a 100%)}
.photo-team{left:0;top:0;width:420px;height:400px;clip-path:path("M0 0 H300 C420 70 420 320 285 375 C200 408 80 400 0 370 Z")}
.photo-circle{border-radius:50%;border:4px solid var(--purple-deep)}
.photo-kids{left:413px;top:300px;width:164px;height:164px;background:linear-gradient(150deg,#c9434f,#e6c34a 45%,#3a5fa8)}
.photo-wash{left:595px;top:328px;width:152px;height:152px;background:linear-gradient(150deg,#7a8c64,#e9e4dc 50%,#3b3b3b)}
.photo-mascot{left:35px;top:610px;width:340px;height:228px;background:linear-gradient(90deg,rgba(120,90,70,.25),rgba(150,110,70,.55) 70%,rgba(210,120,60,.45));border-radius:0 0 8px 8px}
.photo-dog{left:0;top:862px;width:150px;height:233px;background:linear-gradient(170deg,#6b4a2a,#a77a46 55%,#d9c3a0)}
.headline{left:420px;color:var(--white)}
.annual{top:48px;font-family:"Fredoka",sans-serif;font-weight:600;font-size:22px}
.brand{top:96px;font-family:"Montserrat",sans-serif;font-weight:800;font-size:35px;letter-spacing:-.5px;display:flex;align-items:center;gap:10px}
.brand-dot{width:14px;height:14px;border-radius:50%;background:var(--white)}
.motto{top:145px;font-size:11px;font-weight:600;letter-spacing:6.4px}
.title{font-family:"Fredoka",sans-serif;font-weight:700;letter-spacing:1px;line-height:1}
.title-main{top:170px;font-size:40px;color:var(--white)}
.title-sub{top:214px;font-size:34px;color:var(--pink);letter-spacing:.6px}
.tagline{top:260px;font-size:15px;font-weight:700;color:var(--white)}
.perks{left:62px;top:430px;list-style:none;color:var(--white);font-size:15px;font-weight:500}
.perks li{display:flex;align-items:flex-start;gap:12px;height:28.5px}
.perks svg{flex:none;margin-top:2px}
.support{left:420px;top:532px;border:2px solid var(--green-bright);color:var(--pink);font-weight:600;font-size:17px;padding:5px 10px}
.partner{left:585px;top:500px;width:150px;display:flex;align-items:center;gap:8px;font-size:14px;font-weight:700;line-height:1.2;color:var(--ink)}
.partner-mark{flex:none;width:18px;height:18px;background:var(--ink)}
.details{left:418px;font-size:20px;font-weight:600;line-height:1.4;display:flex;gap:16px}
.details svg{flex:none;margin-top:4px}
.when{top:618px}
.year{left:682px;top:620px;width:28px;height:60px;background:var(--green-bright);color:var(--ink);font-weight:700;font-size:18px;writing-mode:vertical-rl;transform:rotate(180deg);display:flex;align-items:center;justify-content:center}
.hours{top:690px}
.where{top:735px;font-weight:500;font-size:18.5px;line-height:1.22}
.donate-line{left:133px;top:874px;font-size:17px;font-weight:400}
.donate-line strong{font-weight:600}
.donate-btn{left:0;width:775px;text-align:center;top:922px;color:var(--pink);font-weight:700;font-size:15px}
.note{left:0;width:775px;text-align:center;top:952px;font-size:12.5px;line-height:1.3}
.contact{top:1004px;font-size:12px;line-height:1.45}
.contact b{font-weight:700;display:block}
.contact-left{left:228px}
.contact-right{left:533px}
.contact-right b{color:var(--navy)}
.mini-logo{font-weight:700;font-size:10.5px;line-height:1.2;display:flex;align-items:center;gap:5px;width:95px}
.mini-square{flex:none;width:10px;height:10px;background:var(--ink)}
.logo-helpers{left:135px;top:1012px}
.logo-realty{left:415px;top:1018px;color:var(--navy)}
.logo-realty .mini-square{background:var(--navy);border-radius:50%}
</style>
</head>
<body>
<main class="flyer">
  <svg class="backdrop" viewBox="0 0 775 1095" aria-hidden="true">
    <path d="M0 0 H775 V402 C700 372 610 362 530 380 C450 398 400 402 375 398 L0 402 Z" fill="var(--green)"/>
    <path d="M312 0 C440 80 432 330 282 388 C200 414 90 410 0 390" fill="none" stroke="var(--pink)" stroke-width="9"/>
    <path d="M23 393 C150 400 280 398 375 392 V830 a10 10 0 0 1 -10 10 H33 a10 10 0 0 1 -10 -10 Z" fill="var(--purple)"/>
    <rect x="0" y="855" width="775" height="84" fill="var(--band)"/>
    <path d="M262 939 C292 939 292 905 325 905 H450 C483 905 483 939 513 939 Z" fill="var(--white)"/>
  </svg>

  <div class="photo photo-team" role="img" aria-label="Photo of volunteers posing with a dog mascot outdoors"></div>
  <div class="photo photo-circle photo-kids" role="img" aria-label="Photo of children with a dog at the event"></div>
  <div class="photo photo-circle photo-wash" role="img" aria-label="Photo of volunteers washing a small dog"></div>
  <div class="photo photo-mascot" role="img" aria-label="Photo of a dog treats tent and a mascot holding a free doggie wash sign"></div>
  <div class="photo photo-dog" role="img" aria-label="Photo of a shepherd dog being brushed"></div>

  <p class="headline annual">Third Annual</p>
  <p class="headline brand"><span>Suds &amp; Wags</span><span class="brand-dot"></span></p>
  <p class="headline motto">DO A LITTLE. CHANGE A LOT.</p>
  <h1 class="headline title title-main">DOGGIE WASH</h1>
  <p class="headline title title-sub">EXTRAVAGANZA</p>
  <p class="headline tagline">A FAMILY FUN EVENT FOR ALL AGES</p>

  <ul class="perks">
    <li><svg width="15" height="15" viewBox="0 0 16 16"><circle cx="8" cy="8" r="6.5" fill="none" stroke="var(--green-bright)" stroke-width="1.6"/><path d="M5 8.2l2 2 4.2-4.4" fill="none" stroke="var(--green-bright)" stroke-width="1.8"/></svg>Free Doggie Wash</li>
    <li><svg width="15" height="15" viewBox="0 0 16 16"><circle cx="8" cy="8" r="6.5" fill="none" stroke="var(--green-bright)" stroke-width="1.6"/><path d="M5 8.2l2 2 4.2-4.4" fill="none" stroke="var(--green-bright)" stroke-width="1.8"/></svg>Food &amp; Beverages</li>
    <li><svg width="15" height="15" viewBox="0 0 16 16"><circle cx="8" cy="8" r="6.5" fill="none" stroke="var(--green-bright)" stroke-width="1.6"/><path d="M5 8.2l2 2 4.2-4.4" fill="none" stroke="var(--green-bright)" stroke-width="1.8"/></svg>Vendors (Free give-a-ways)</li>
    <li><svg width="15" height="15" viewBox="0 0 16 16"><circle cx="8" cy="8" r="6.5" fill="none" stroke="var(--green-bright)" stroke-width="1.6"/><path d="M5 8.2l2 2 4.2-4.4" fill="none" stroke="var(--green-bright)" stroke-width="1.8"/></svg>Raffle drawings</li>
    <li><svg width="15" height="15" viewBox="0 0 16 16"><circle cx="8" cy="8" r="6.5" fill="none" stroke="var(--green-bright)" stroke-width="1.6"/><path d="M5 8.2l2 2 4.2-4.4" fill="none" stroke="var(--green-bright)" stroke-width="1.8"/></svg>Live Music</li>
    <li><svg width="15" height="15" viewBox="0 0 16 16"><circle cx="8" cy="8" r="6.5" fill="none" stroke="var(--green-bright)" stroke-width="1.6"/><path d="M5 8.2l2 2 4.2-4.4" fill="none" stroke="var(--green-bright)" stroke-width="1.8"/></svg>Donations Welcome</li>
    <li><svg width="15" height="15" viewBox="0 0 16 16"><circle cx="8" cy="8" r="6.5" fill="none" stroke="var(--green-bright)" stroke-width="1.6"/><path d="M5 8.2l2 2 4.2-4.4" fill="none" stroke="var(--green-bright)" stroke-width="1.8"/></svg><span>Adoptions by<br>HTVPC</span></li>
  </ul>

  <p class="support">In support of</p>
  <p class="partner"><span class="partner-mark"></span><span>Helpers of Tamsin Valley Pet Center</span></p>

  <div class="details when">
    <svg width="22" height="22" viewBox="0 0 22 22"><rect x="2" y="4" width="18" height="16" rx="2" fill="none" stroke="var(--pink)" stroke-width="1.8"/><path d="M2 9h18M7 2v4M15 2v4" stroke="var(--pink)" stroke-width="1.8"/><path d="M6 12h2M10 12h2M14 12h2M6 16h2M10 16h2M14 16h2" stroke="var(--pink)" stroke-width="1.6"/></svg>
    <p>Saturday April 25th<br>Rain Date May 2nd</p>
  </div>
  <p class="year">2020</p>
  <div class="details hours">
    <svg width="22" height="22" viewBox="0 0 22 22"><circle cx="11" cy="11" r="9" fill="none" stroke="var(--pink)" stroke-width="2"/><path d="M11 6v5.5l3.5 2" fill="none" stroke="var(--pink)" stroke-width="2"/></svg>
    <p>10am - 1pm</p>
  </div>
  <div class="details where">
    <svg width="22" height="30" viewBox="0 0 22 30"><path d="M11 2a8 8 0 0 0-8 8c0 6 8 13 8 13s8-7 8-13a8 8 0 0 0-8-8z" fill="none" stroke="var(--pink)" stroke-width="2.6"/><circle cx="11" cy="10" r="3" fill="var(--pink)"/><path d="M11 23v6" stroke="var(--pink)" stroke-width="2.6"/></svg>
    <p>Harbor Lane Realty<br>418 Cedar Market Way<br>Tamsin Valley, FL 32190<br>Brookfield Town Center</p>
  </div>

  <p class="donate-line">TO MAKE A DONATION:&nbsp; <strong>https://www.sudsandwags.org/give/</strong></p>
  <p class="donate-btn">CLICK: DONATE</p>
  <p class="note">All Domestic breeds from puppies to seniors invited. Please be sure <i>furryfido</i><br>tolerant of other dogs, crowds and bathing</p>

  <p class="mini-logo logo-helpers"><span class="mini-square"></span><span>Helpers of Tamsin Valley</span></p>
  <p class="contact contact-left"><b>MAREN HOLLOWAY</b>HTVPC<br>555.014.2287<br>maren-holloway@wagmail.net</p>
  <p class="mini-logo logo-realty"><span class="mini-square"></span><span>Harbor Lane Realty</span></p>
  <p class="contact contact-right"><b>DELLA PRESCOTT</b>Harbor Lane Realty<br>555.019.4410<br>della@harborlanerealty.com</p>
</main>
</body>
</html>
```